Hearthline Insurance Provider Website

We are selling Hearthline Insurance policy / tenants Policy/Flood Insurance in USA in few states and planning expand nationally.

Our target audience are two folds: Customers (Buy policies) and Insurance Agents who wants to work with us to sell our policies to customers. But website should focus 80% on customers and 20% on agents. So, more customer focused user experience. Please note that there is no direct buy option for customers. They always go through insurance agents.

Customer focused, educational that makes buyer journey easy. We don’t want to come off as trying sell something as there is no direct sales involved from website.

Target Market(s)

Homeowners in USA and Insurance agent who sells these insurance.

Industry/Entity Type

Insurance

Number of Pages Required

4 page

Font styles to use
Other font styles liked:
• Open to suggestions

Colors

Designer to choose colors to be used in the design.

Requirements
Must have
• Three most important things: Trustworthy, Authentic, Simple
• Please use colors form logo and grays
• We like: www.hollowmere.com
• https://www.quillfenbrook.com/
• We need Agent Look up tool on home page similar to what is shown on example sites.
• Design:
• Home Page - Open to Ideas
• Insurance (Products) Landing Page - Info similar to: https://www.quillfenbrook.com/insurance/
• Agents Page - https://www.quillfenbrook.com/agents/
• Claims Page - Information similar to: https://www.quillfenbrook.com/claims-center/
• Site Navigation:
• Home
• Insurance
• Claims
• Agents
• About Us
• Contact Us
Nice to have
• Elegant, minimal and clean design that reflects trust and authenticity.
Should not have
• Slider or rotating images - prefer flat design. Not over powering design.

```html
<!DOCTYPE html>
<html lang="en">
<head>
<meta charset="utf-8">
<title>Hearthline Insurance Co. — Home</title>
<link rel="stylesheet" href="https://fonts.googleapis.com/css2?family=Open+Sans:wght@400;600;700;800&family=Raleway:wght@400;500;600&display=swap">
<style>
:root{
  --red:#d71f2b;
  --navy:#233c86;
  --navy-deep:#1b2a5c;
  --ink:#222;
  --text:#444;
  --muted:#777;
  --line:#d8d8d8;
  --light:#f3f3f3;
  --footer:#1d1d1d;
  --white:#fff;
}
*{box-sizing:border-box;margin:0;padding:0}
html,body{width:1200px;height:2903px;overflow:hidden}
body{position:relative;font-family:"Raleway",sans-serif;color:var(--text);background:var(--white)}
.abs{position:absolute}
h1,h2,h3,h4{font-family:"Open Sans",sans-serif;font-weight:600;color:var(--ink)}
.btn{position:absolute;display:flex;align-items:center;justify-content:center;font-family:"Open Sans",sans-serif;font-size:12px;font-weight:600;letter-spacing:.5px;text-transform:uppercase;color:var(--white)}
.btn-red{background:var(--red)}
.btn-navy{background:var(--navy)}
.btn-ghost{border:1px solid rgba(255,255,255,.85)}
.btn-white{background:var(--white);color:var(--red)}

/* Header + hero */
.hero-photo{left:0;top:0;width:1200px;height:548px;background:linear-gradient(110deg,#d9dee2 0%,#b9c2c9 35%,#59606a 62%,#2f3440 78%,#c9ced3 100%)}
.site-header{left:0;top:0;width:1200px;height:85px;background:rgba(255,255,255,.9)}
.brand{left:150px;top:22px;display:flex;align-items:center;gap:12px}
.brand-mark{width:40px;height:40px;background:var(--navy)}
.brand-name{font-family:"Open Sans",sans-serif;font-weight:700;font-size:24px;color:var(--navy);line-height:1.05}
.brand-name small{display:block;font-size:15px;letter-spacing:3px;font-weight:700}
.main-nav{left:574px;top:30px;display:flex;align-items:center;gap:20px;font-size:13px;color:#333}
.main-nav .active{color:var(--red)}
.main-nav .cta{background:var(--navy);color:var(--white);padding:6px 10px}

.policy-badge{width:194px;height:194px;border-radius:50%;background:rgba(255,255,255,.55);top:451px}
.policy-badge .inner{position:absolute;left:12px;top:12px;width:170px;height:170px;border-radius:50%;background:var(--white);border:2px solid #eee;display:flex;align-items:center;justify-content:center}
.policy-label{top:632px;width:260px;text-align:center;font-family:"Open Sans",sans-serif;font-weight:600;font-size:15px;color:var(--red);line-height:21px;text-transform:uppercase}

/* About */
.section-title{font-size:26px;letter-spacing:1px;text-transform:uppercase}
.about-title{left:143px;top:730px}
.about-rule{left:143px;top:784px;width:615px;height:1px;background:var(--line)}
.about-rule::before{content:"";position:absolute;left:0;top:-2px;width:62px;height:4px;background:var(--navy)}
.about-copy{left:143px;top:808px;width:615px;font-size:12.5px;line-height:23.5px}

.quote-form{left:818px;top:720px;width:240px;height:282px;background:#f4f4f4;border:1px solid #e2e2e2}
.quote-form h3{height:36px;background:var(--red);color:var(--white);font-size:20px;font-weight:600;display:flex;align-items:center;justify-content:center}
.field{position:absolute;background:var(--white);border:1px solid #ddd;font-size:10px;color:#999;padding:0 10px;display:flex;align-items:center}
.quote-form .field{left:14px;width:212px;height:30px}

/* Split band */
.split{top:1060px;width:600px;height:325px;text-align:center;color:var(--white)}
.split-customers{left:0;background:linear-gradient(90deg,#2b2b2b,#565656 55%,#3a3a3a)}
.split-agents{left:600px;width:600px;background:linear-gradient(90deg,#c8202a,#e5333d 50%,#b71a23)}
.split h3{color:var(--white);font-size:21px;margin-top:10px}
.split p{width:330px;margin:10px auto 0;font-size:12.5px;line-height:23px}
.split .icon{margin-top:40px;height:60px;display:flex;justify-content:center;align-items:flex-end}

/* Insurance */
.insurance{left:0;top:1385px;width:1200px;height:635px;background:var(--light)}
.insurance-title{left:0;top:1432px;width:1200px;text-align:center}
.insurance-rule{left:292px;top:1490px;width:615px;height:1px;background:#bbb}
.insurance-rule::before{content:"";position:absolute;left:277px;top:-2px;width:62px;height:4px;background:var(--navy)}
.policy-card{top:1544px;width:306px;height:412px;color:var(--white);text-align:center;overflow:hidden}
.policy-card .photo{position:absolute;inset:0}
.policy-card .body{position:absolute;left:0;bottom:0;width:100%}
.policy-card h4{color:var(--white);font-size:20px;font-weight:600}
.policy-card h4::after{content:"";display:block;width:40px;height:2px;background:var(--red);margin:10px auto 0}
.policy-card p{width:270px;margin:10px auto 0;font-size:11px;line-height:20px}
.policy-card .actions{position:relative;height:30px;margin:20px 0 27px}
.policy-card .btn{height:30px;top:0}

/* Agent finder */
.finder{left:0;top:2020px;width:1200px;height:292px;background:var(--navy-deep);color:var(--white);text-align:center}
.finder h2{color:var(--white);font-size:25px;letter-spacing:1px;text-transform:uppercase;margin-top:52px}
.finder .rule{width:62px;height:3px;background:var(--white);margin:12px auto 0}
.finder p{width:610px;margin:18px auto 0;font-size:12.5px;line-height:23px}
.finder-input{left:439px;top:213px;width:157px;height:29px;background:var(--white);color:#999;font-size:11px;text-align:left;padding:0 10px;display:flex;align-items:center}

/* Claim + contact */
.claim{left:140px;top:2362px;width:300px;text-align:center}
.claim h3{font-size:27px;color:var(--navy-deep);font-weight:600}
.claim .big{font-family:"Open Sans",sans-serif;font-weight:800;font-size:58px;color:var(--red);line-height:66px}
.claim p{font-size:14px;line-height:25px;color:var(--navy-deep);margin-top:6px}
.divider{left:441px;top:2340px;width:1px;height:240px;background:var(--line)}
.contact-title{left:486px;top:2360px;font-size:27px;font-weight:500;text-transform:uppercase}
.contact-rule{left:486px;top:2410px;width:572px;height:1px;background:var(--line)}
.contact-rule::before{content:"";position:absolute;left:0;top:-2px;width:62px;height:4px;background:var(--navy)}
.contact-hint{left:486px;top:2424px;font-size:11px}
.contact .field{height:32px;border-color:#ccc}

/* Footer */
.footer{left:0;top:2618px;width:1200px;height:248px;background:var(--footer);color:#bbb}
.footer h4{color:var(--white);font-size:16px;font-weight:500;position:absolute;top:48px}
.footer .frule{position:absolute;top:78px;height:1px;background:#444}
.quick-links{position:absolute;left:160px;top:100px;list-style:none;font-size:11px;line-height:21.5px}
.quick-links li::before{content:"›";margin-right:6px;color:#888}
.quick-links .current{color:var(--navy)}
.footer .detail{position:absolute;left:339px;top:92px;width:240px;font-size:11px;line-height:18px}
.footer .detail strong{color:var(--white);font-weight:500}
.footer .line-item{position:absolute;left:339px;display:flex;align-items:center;gap:12px}
.newsletter{position:absolute;left:623px;top:100px;width:210px;font-size:11px;line-height:20px}
.footer-name{position:absolute;left:885px;top:112px;width:210px;font-family:"Open Sans",sans-serif;font-weight:700;font-size:19px;color:#ccc;text-align:center}
.bottom-bar{left:0;top:2866px;width:1200px;height:37px;background:var(--navy);color:var(--white);font-size:11px;font-weight:600}
.social{position:absolute;top:8px;width:21px;height:21px;border:1px solid var(--white)}
</style>
</head>
<body>

<!-- Header + hero -->
<div class="abs hero-photo" role="img" aria-label="Smiling insurance advisor in a suit in a bright office"></div>
<header class="abs site-header">
  <div class="abs brand">
    <span class="brand-mark"></span>
    <span class="brand-name">HEARTHLINE<small>INSURANCE CO.</small></span>
  </div>
  <nav class="abs main-nav">
    <span class="active">Home</span><span>About Us</span><span>Insurance</span><span>Agents</span><span>Claims</span><span>Contact Us</span><span class="cta">Get a quote</span>
  </nav>
</header>

<div class="abs policy-badge" style="left:216px"><div class="inner">
  <svg width="62" height="62" viewBox="0 0 62 62"><path d="M10 30 L31 10 L52 30 L47 30 L47 44 L15 44 L15 30 Z" fill="var(--red)"/><circle cx="26" cy="28" r="3" fill="#fff"/><circle cx="36" cy="38" r="3" fill="#fff"/><path d="M38 25 L24 41" stroke="#fff" stroke-width="2.5"/><path d="M4 52 Q18 44 30 50 L46 50 Q50 52 46 55 L22 56" fill="none" stroke="var(--red)" stroke-width="3"/></svg>
</div></div>
<div class="abs policy-badge" style="left:503px"><div class="inner">
  <svg width="62" height="62" viewBox="0 0 62 62"><path d="M6 28 L31 6 L56 28 L50 28 L50 56 L12 56 L12 28 Z" fill="var(--red)"/><circle cx="25" cy="28" r="4" fill="#fff"/><circle cx="37" cy="28" r="4" fill="#fff"/><rect x="20" y="34" width="10" height="18" rx="2" fill="#fff"/><rect x="32" y="34" width="10" height="18" rx="2" fill="#fff"/></svg>
</div></div>
<div class="abs policy-badge" style="left:783px"><div class="inner">
  <svg width="62" height="62" viewBox="0 0 62 62"><path d="M8 30 L31 10 L54 30 L48 30 L48 42 L14 42 L14 30 Z" fill="var(--red)"/><rect x="27" y="30" width="8" height="12" fill="#fff"/><path d="M4 48 q6 -5 12 0 t12 0 t12 0 t12 0 t6 0 M4 55 q6 -5 12 0 t12 0 t12 0 t12 0 t6 0" fill="none" stroke="var(--red)" stroke-width="3"/></svg>
</div></div>
<div class="abs policy-label" style="left:183px">Homeowners<br>Policy</div>
<div class="abs policy-label" style="left:470px;top:643px">Tenants Policy</div>
<div class="abs policy-label" style="left:750px;top:643px">Flood Insurance</div>

<!-- About -->
<h2 class="abs section-title about-title">About Us</h2>
<div class="abs about-rule"></div>
<p class="abs about-copy">Lorem ipsum dolor sit amet, consectetuer adipiscing elit, sed diam nonummy nibh euismod tincidunt ut laoreet dolore magna aliquam erat volutpat. Ut wisi enim ad minim veniam, quis nostrud exerci tation ullamcorper suscipit lobortis nisl ut aliquip ex ea commodo consequat. Duis autem vel eum iriure dolor in hendrerit in vulputate velit esse molestie consequat, vel illum dolore eu feugiat nulla facilisis at vero eros et accumsan et iusto odio dignissim qui blandit praesent luptatum zzril delenit augue duis dolore te feugait nulla facilisi.</p>
<span class="btn btn-navy" style="left:143px;top:971px;width:128px;height:28px">Read More</span>

<form class="abs quote-form">
  <h3>Get A Quote</h3>
  <span class="field" style="top:57px">Name</span>
  <span class="field" style="top:94px">Email</span>
  <span class="field" style="top:131px">Subject</span>
  <span class="field" style="top:168px;height:50px">Message</span>
  <span class="btn btn-navy" style="left:14px;top:228px;width:212px;height:32px">Submit</span>
</form>

<!-- Customers / Agents -->
<section class="abs split split-customers" role="img" aria-label="Customers shaking hands with an advisor at a table">
  <div class="icon"><svg width="72" height="40" viewBox="0 0 72 40"><path d="M2 10 L16 6 L30 14 L44 8 L58 4 L70 10 L66 24 L48 36 L30 34 L14 24 Z" fill="#fff"/><path d="M26 20 L38 30 M32 16 L44 26" stroke="#4a4a4a" stroke-width="2"/></svg></div>
  <h3>Customers</h3>
  <p>Lorem ipsum dolor sit amet, consectetuer adipiscing elit, sed diam nonummy nibh euismod tincidunt ut laoreet dolore magna aliquam erat volutpat</p>
  <span class="btn btn-ghost" style="left:304px;top:240px;width:130px;height:29px">Read More</span>
</section>
<section class="abs split split-agents" role="img" aria-label="Insurance agent working at a desk">
  <div class="icon" style="margin-top:36px"><svg width="68" height="68" viewBox="0 0 68 68"><circle cx="34" cy="34" r="33" fill="#fff"/><circle cx="34" cy="22" r="7" fill="var(--red)"/><path d="M22 46 q12 -20 24 0 Z" fill="var(--red)"/><circle cx="18" cy="30" r="5" fill="var(--red)"/><circle cx="50" cy="30" r="5" fill="var(--red)"/><path d="M9 48 q9 -14 18 0 Z M41 48 q9 -14 18 0 Z" fill="var(--red)"/></svg></div>
  <h3 style="margin-top:4px">Agents</h3>
  <p>Lorem ipsum dolor sit amet, consectetuer adipiscing elit, sed diam nonummy nibh euismod tincidunt ut laoreet dolore magna aliquam erat volutpat</p>
  <span class="btn btn-ghost" style="left:164px;top:240px;width:130px;height:29px">Read More</span>
</section>

<!-- Insurance -->
<div class="abs insurance"></div>
<h2 class="abs section-title insurance-title">Insurance</h2>
<div class="abs insurance-rule"></div>

<article class="abs policy-card" style="left:141px">
  <div class="photo" role="img" aria-label="Couple looking around a new bright home" style="background:linear-gradient(180deg,#e6e6e6 0%,#b9b6b2 40%,#3a3a3a 68%,#151515 100%)"></div>
  <div class="body">
    <h4>Homeowner Policy</h4>
    <p>Lorem ipsum dolor sit amet, consectetuer adipiscing elit, sed diam nonummy nibh euismod tincidunt ut laoreet dolore magna aliquam erat volutpat</p>
    <div class="actions"><span class="btn btn-red" style="left:29px;width:108px">Quote →</span><span class="btn btn-navy" style="left:146px;width:130px">Read More →</span></div>
  </div>
</article>
<article class="abs policy-card" style="left:447px">
  <div class="photo" role="img" aria-label="Young tenants smiling together" style="background:linear-gradient(180deg,#d8c7b0 0%,#b89878 50%,#a5876a 100%)"></div>
  <div class="body" style="height:214px;background:rgba(35,60,134,.92);padding-top:22px">
    <h4>Tenant Policy</h4>
    <p>Lorem ipsum dolor sit amet, consectetuer adipiscing elit, sed diam nonummy nibh euismod tincidunt ut laoreet dolore magna aliquam erat volutpat</p>
    <div class="actions" style="margin-top:18px"><span class="btn btn-red" style="left:29px;width:108px">Quote →</span><span class="btn btn-white" style="left:146px;width:130px">Read More →</span></div>
  </div>
</article>
<article class="abs policy-card" style="left:753px">
  <div class="photo" role="img" aria-label="Flooded red house among green trees" style="background:linear-gradient(180deg,#5d7a3c 0%,#7a4a3c 40%,#2e2a26 68%,#151515 100%)"></div>
  <div class="body">
    <h4>Flood Policy</h4>
    <p>Lorem ipsum dolor sit amet, consectetuer adipiscing elit, sed diam nonummy nibh euismod tincidunt ut laoreet dolore magna aliquam erat volutpat</p>
    <div class="actions"><span class="btn btn-red" style="left:29px;width:108px">Quote →</span><span class="btn btn-navy" style="left:146px;width:130px">Read More →</span></div>
  </div>
</article>

<!-- Find an agent -->
<section class="abs finder">
  <h2>Find An Agent</h2>
  <div class="rule"></div>
  <p>Lorem ipsum dolor sit amet, consectetuer adipiscing elit, sed diam nonummy nibh euismod tincidunt ut laoreet dolore magna aliquam erat volutpat. Ut wisi enim ad minim veniam, quis nostrud exerci tation ullamcorper suscipit lobortis nisl ut aliquip ex ea commodo consequat.</p>
  <span class="abs finder-input">Search...</span>
  <span class="btn btn-red" style="left:604px;top:213px;width:156px;height:29px">Find An Agent</span>
</section>

<!-- Claim -->
<section class="abs claim">
  <h3>Report And Check</h3>
  <div class="big">A Claim</div>
  <p>Login To Report A Claim Or<br>Check Your Claim Status.</p>
</section>
<span class="btn btn-red" style="left:238px;top:2539px;width:85px;height:29px">Login</span>
<div class="abs divider"></div>

<!-- Contact -->
<h2 class="abs contact-title">Contact Form</h2>
<div class="abs contact-rule"></div>
<p class="abs contact-hint">Please fill up bellow form</p>
<div class="contact">
  <span class="field" style="left:484px;top:2446px;width:257px">Name</span>
  <span class="field" style="left:753px;top:2446px;width:257px">Email</span>
  <span class="field" style="left:484px;top:2490px;width:257px">Phone</span>
  <span class="field" style="left:753px;top:2490px;width:257px">Message</span>
</div>
<span class="btn btn-red" style="left:484px;top:2539px;width:87px;height:29px">Submit</span>

<!-- Footer -->
<footer class="abs footer">
  <h4 style="left:160px">Quick Links</h4><div class="frule" style="left:160px;width:100px"></div>
  <ul class="quick-links"><li class="current">Home</li><li>About Us</li><li>Insurance</li><li>Agents</li><li>Claims</li><li>Contact Us</li></ul>

  <h4 style="left:339px">Contact Detail</h4><div class="frule" style="left:339px;width:185px"></div>
  <div class="detail"><strong>Hearthline Insurance</strong><br>Lorem ipsum dolor sit amet, consectetuer<br>adipiscing elit, sed do euismod</div>
  <div class="line-item" style="top:160px;font-size:15px"><svg width="14" height="14" viewBox="0 0 14 14"><path d="M3 1 L5 1 L6 4 L4.5 5.5 Q6 8.5 8.5 9.5 L10 8 L13 9 L13 11 Q13 13 11 13 Q1 12 1 3 Q1 1 3 1 Z" fill="var(--navy)"/></svg>800.555.0142</div>
  <div class="line-item" style="top:199px;font-size:11px"><svg width="14" height="11" viewBox="0 0 14 11"><rect x="0.5" y="0.5" width="13" height="10" fill="var(--navy)"/><path d="M1 1 L7 6 L13 1" stroke="#fff" fill="none"/></svg>info@hearthline.com</div>

  <h4 style="left:623px">Join Our Newsletter</h4><div class="frule" style="left:623px;width:215px"></div>
  <p class="newsletter">Subscribe to our Newsletter to get the latest scoop right to your inbox</p>
  <span class="field" style="left:623px;top:143px;width:172px;height:30px;background:#3a3a3a;border-color:#3a3a3a;color:#ccc">Enter Your Email</span>
  <span class="btn btn-red" style="left:623px;top:186px;width:93px;height:28px;text-transform:none;font-size:12px">Subscribe</span>

  <div class="footer-name">Hearthline<br>Insurance Co.</div>
</footer>
<div class="abs bottom-bar">
  <span class="abs" style="left:143px;top:11px">© 2018 Hearthlineinsurance.com. All Rights Reserved.</span>
  <span class="social" style="left:980px"></span>
  <span class="social" style="left:1008px"></span>
  <span class="social" style="left:1036px"></span>
</div>

</body>
</html>
```